Design a single page Shopify store web page

We are looking to have a page designed for a single page Shopify store with 2 products. We already have a basic structure that we like, though we are open to suggestions. We are looking for somebody to provide a design/color scheme that we can then implement using Shopify's templating system. We can handle the implementation(HTML / CSS / jS) as we already have 2 web developers on the team, but have not been able to find a design we liked.

The job would consist of providing a mockup (photoshop or otherwise) and any vector graphics you choose to create for the site (we can provide product photos and other images).

You can also look at http://brickdune.com.au for some of our design direction we have used so far

Target Market(s)

Young Australian Males (18 - 49)

Industry/Entity Type

Store

Number of Pages Required

1 page

Font styles to use
Serif
Sans Serif

Requirements
Must have
• Single Page Design
• E-commerce Product Purchase
• Manly (whatever interpretation of that you have)

```html
<!DOCTYPE html>
<html lang="en">
<head>
<meta charset="utf-8">
<title>Brick Dune – Underwear and Socks Plans</title>
<link href="https://fonts.googleapis.com/css2?family=Signika:wght@300;400;600;700&display=swap" rel="stylesheet">
<style>
:root{
  --black:#050505;
  --gold:#f2c11d;
  --gold-deep:#e8b417;
  --sky:#1ea6ee;
  --sky-light:#34b8f4;
  --sky-dark:#1488d4;
  --orange-btn:#f7b526;
  --salmon:#d98569;
  --salmon-dark:#b8624a;
  --bar:rgba(90,45,35,.78);
  --blue-btn:#1d6fd6;
  --white:#ffffff;
  --ink:#4a4a4a;
  --faq-text:#dff2ff;
}
*{box-sizing:border-box;margin:0;padding:0}
html,body{width:720px;height:1200px;overflow:hidden;background:#fff}
body{font-family:"Signika",sans-serif;position:relative}
.abs{position:absolute}

/* header */
.site-header{position:absolute;left:0;top:0;width:720px;height:56px;background:var(--black)}
.brand{position:absolute;left:56px;top:14px;display:flex;align-items:center;gap:8px;color:#cfcfcf;font-weight:300;font-size:24px;letter-spacing:1px}
.brand-mark{width:14px;height:14px;border-radius:50%;background:#cfcfcf}
.main-nav{position:absolute;left:292px;top:20px;display:flex;gap:22px;font-size:12px;color:var(--white);font-weight:300}
.signup{position:absolute;left:548px;top:17px;width:82px;height:25px;border:1px solid var(--gold);border-radius:3px;color:var(--gold);font-size:11.5px;font-weight:600;display:flex;align-items:center;justify-content:center}

/* hero */
.hero{position:absolute;left:0;top:56px;width:720px;height:309px;background:radial-gradient(ellipse at 65% 35%,var(--sky-light),var(--sky) 55%,var(--sky-dark))}
.hero-photo{position:absolute;left:95px;top:54px;width:266px;height:196px;border-radius:10px;background:linear-gradient(135deg,#f5c630,#f08a2a 45%,#e33a4a 75%,#f47ca0)}
.hero-title{position:absolute;left:350px;top:99px;width:320px;text-align:center;color:var(--white);font-weight:300;font-size:27px;line-height:30px}
.hero-cta{position:absolute;left:440px;top:212px;width:128px;height:39px;background:var(--orange-btn);border-radius:3px;color:#4a3200;font-weight:600;font-size:19px;display:flex;align-items:center;justify-content:center;box-shadow:0 2px 3px rgba(0,0,0,.2)}
.slider-dots{position:absolute;left:110px;top:273px;display:flex;gap:4px}
.slider-dots span{width:8px;height:8px;border-radius:50%;background:#111}
.slider-dots span.on{background:var(--gold)}

/* how it works */
.how{position:absolute;left:0;top:365px;width:720px;height:238px;background:#fff;overflow:hidden}
.how h2{position:absolute;left:0;width:720px;top:18px;text-align:center;font-size:30px;font-weight:600;color:var(--ink)}
.socks-photo{position:absolute;left:490px;top:20px;width:175px;height:218px;border-radius:40px 40px 0 0;background:linear-gradient(160deg,#e53a3a,#f4a21e 30%,#2fa0e0 55%,#7a3fb0 75%,#f2d21e)}
.step{position:absolute;top:83px;width:128px;height:118px;background:linear-gradient(135deg,var(--gold),var(--gold-deep));color:var(--white);text-align:center;padding-top:22px}
.step h3{font-size:19px;line-height:21px;font-weight:600}
.step p{margin:9px 14px 0;padding:0 6px;font-size:7.5px;line-height:9.5px;color:#5a4300;border-left:1px solid #fff;border-right:1px solid #fff}

/* plans */
.plans{position:absolute;left:0;top:603px;width:720px;height:310px;background:linear-gradient(120deg,var(--salmon),#e89b7f 45%,var(--salmon-dark))}
.plans-title{position:absolute;left:82px;top:13px;width:582px;height:33px;background:var(--bar);color:var(--white);font-size:28px;font-weight:600;text-align:center;line-height:33px}
.plan-label{position:absolute;top:54px;color:var(--white);font-size:15px}
.plan-photo{position:absolute;top:75px;width:179px;height:179px;border:2px solid #eee;background:linear-gradient(160deg,#d9d9d9,#9a9ea4)}
.chip{position:absolute;width:59px;height:18px;border-radius:2px;font-size:8.5px;display:flex;align-items:center;justify-content:center;color:#333}
.chip.cart{background:#f4f4f4}
.chip.details{background:var(--gold);height:16px}
.price{position:absolute;top:143px;color:var(--white);font-weight:600;font-size:33px}
.get-it{position:absolute;top:209px;width:87px;height:26px;background:var(--blue-btn);border-radius:3px;color:var(--white);font-size:15px;font-weight:600;display:flex;align-items:center;justify-content:center}
.perks{position:absolute;left:78px;top:268px;width:582px;height:34px;background:var(--bar);display:flex;align-items:center;color:var(--white);font-size:10px;font-weight:600}
.perks span{position:absolute}
.perks span::before{content:"";display:inline-block;width:6px;height:6px;border-radius:50%;background:#fff;margin-right:8px;vertical-align:1px}

/* faq */
.faq{position:absolute;left:0;top:913px;width:720px;height:239px;background:var(--sky)}
.faq h2{position:absolute;left:0;width:720px;top:6px;text-align:center;color:var(--white);font-size:30px;font-weight:600}
.faq-item{position:absolute;width:170px;text-align:center;color:var(--white)}
.faq-item h3{font-size:12.5px;line-height:14px;font-weight:600;margin-bottom:6px}
.faq-item p{font-size:7.5px;line-height:9.5px;color:var(--faq-text);font-weight:300}

/* footer */
.site-footer{position:absolute;left:0;top:1152px;width:720px;height:48px;background:var(--black)}
.legal-links{position:absolute;left:73px;top:22px;font-size:8.5px;color:var(--gold)}
.social{position:absolute;left:453px;top:8px;display:flex;gap:6px}
.social span{width:19px;height:19px;border-radius:2px;background:#2d7fd0}
.cards{position:absolute;left:572px;top:10px;display:flex;gap:4px}
.cards span{width:24px;height:15px;border-radius:2px;background:#3a8fe0}
.copyright{position:absolute;left:430px;top:36px;font-size:7.5px;color:#bbb}
</style>
</head>
<body>

<header class="site-header">
  <div class="brand"><span>BRICK</span><span class="brand-mark"></span><span>DUNE</span></div>
  <nav class="main-nav"><span>How it works</span><span>Plans</span><span>FAQ</span><span>About Us</span></nav>
  <div class="signup">Signup Now</div>
</header>

<section class="hero">
  <div class="hero-photo" role="img" aria-label="Orange and yellow boxer shorts with red and pink striped socks"></div>
  <h1 class="hero-title">New Underwear and Socks<br>Delivered to your door<br>Every 3 or 6 Months</h1>
  <div class="hero-cta">Yes Please!</div>
  <div class="slider-dots"><span></span><span></span><span></span><span class="on"></span></div>
</section>

<section class="how">
  <div class="socks-photo" role="img" aria-label="Legs in rainbow striped toe socks"></div>
  <h2>How it Works</h2>
  <div class="step" style="left:146px"><h3>CHOOSE A<br>PLAN</h3><p>There will be plans for all budgets and styles.</p></div>
  <div class="step" style="left:296px"><h3>CHOOSE<br>HOW OFTEN</h3><p>Decide whether you would like to receive new packages every 3 or 6 months.</p></div>
  <div class="step" style="left:446px"><h3>GET YOUR<br>PACK</h3><p>We'll send out your first pack right away and then again every 3 or 6 months.</p></div>
</section>

<section class="plans" role="img" aria-label="Couple with bicycles in front of a terracotta wall, warm tinted backdrop">
  <div class="plans-title">Plans</div>

  <div class="plan-label" style="left:82px">Comfort</div>
  <div class="plan-photo" style="left:80px" role="img" aria-label="Man relaxing on a bed in a t-shirt and boxers"></div>
  <div class="chip cart" style="left:266px;top:85px">Cart</div>
  <div class="chip details" style="left:266px;top:111px">Details</div>
  <div class="price" style="left:270px">$30</div>
  <div class="get-it" style="left:118px">GET IT</div>

  <div class="plan-label" style="left:390px">Style</div>
  <div class="plan-photo" style="left:389px" role="img" aria-label="Man posing in white trunks"></div>
  <div class="chip cart" style="left:576px;top:85px">Cart</div>
  <div class="chip details" style="left:576px;top:111px">Details</div>
  <div class="price" style="left:578px">$30</div>
  <div class="get-it" style="left:439px">GET IT</div>

  <div class="perks">
    <span style="left:35px">FREE SHIPPING</span>
    <span style="left:142px">EASY RETURNS</span>
    <span style="left:256px">CANCEL WHENEVER</span>
    <span style="left:396px">SATISFACTION GUARANTEED</span>
  </div>
</section>

<section class="faq">
  <h2>FAQ</h2>
  <div class="faq-item" style="left:72px;top:55px"><h3>What is Brick Dune?</h3><p>Nemo enim ipsam voluptatem quia voluptas sit aspernatur aut odit aut fugit, sed quia consequuntur magni dolores eos qui ratione voluptatem sequi nesciunt.</p></div>
  <div class="faq-item" style="left:277px;top:55px"><h3>What is Your<br>Satisfaction Guarantee?</h3><p>Nemo enim ipsam voluptatem quia voluptas sit aspernatur aut odit aut fugit, sed quia consequuntur magni dolores eos qui ratione voluptatem sequi nesciunt.</p></div>
  <div class="faq-item" style="left:482px;top:55px"><h3>Shipping Policy</h3><p>Nemo enim ipsam voluptatem quia voluptas sit aspernatur aut odit aut fugit, sed quia consequuntur magni dolores eos qui ratione voluptatem sequi nesciunt.</p></div>
  <div class="faq-item" style="left:72px;top:150px"><h3>What do i get with my<br>Brick Dune Plan</h3><p>Nemo enim ipsam voluptatem quia voluptas sit aspernatur aut odit aut fugit, sed quia consequuntur magni dolores eos qui ratione voluptatem sequi nesciunt.</p></div>
  <div class="faq-item" style="left:277px;top:141px"><h3>Return Policy</h3><p style="margin-top:14px">Nemo enim ipsam voluptatem quia voluptas sit aspernatur aut odit aut fugit, sed quia consequuntur magni dolores eos qui ratione voluptatem sequi nesciunt.</p></div>
  <div class="faq-item" style="left:482px;top:141px"><h3>What Brands do you<br>Stock?</h3><p>Nemo enim ipsam voluptatem quia voluptas sit aspernatur aut odit aut fugit, sed quia consequuntur magni dolores eos qui ratione voluptatem sequi nesciunt.</p></div>
</section>

<footer class="site-footer">
  <div class="legal-links">Shipping / Returns / Payment / Terms / Privacy</div>
  <div class="social"><span></span><span></span><span></span><span></span></div>
  <div class="cards"><span></span><span></span><span></span></div>
  <div class="copyright">Copyright © 2014 www.brickdune.com.au. All rights reserved.</div>
</footer>

</body>
</html>
```